Spring Detox sale graphics for social media

You MUST read the Brief in the WORD document and follow the instructions there. I want to create 10 social media graphics (new Instagram size 4:5 (1080 x 1350 pixels) focusing on our Mother’s Day Spring Detox Sale graphics, using any of the pics attached. Use the attached pics, NO RANDOM STOCK PHOTOGRAPHY. For the color scheme of the graphics, they should all be complementary to the product colors or feel like Spring time.

Target Market(s)

primarily women

Requirements
Must have
• the photos and text attached

```html
<!DOCTYPE html>
<html lang="en">
<head>
<meta charset="utf-8">
<title>Mother's Day Spring Detox Sale – Social Set</title>
<link href="https://fonts.googleapis.com/css2?family=Playfair+Display:wght@700;800&family=Montserrat:wght@500;600;700;800&family=Bebas+Neue&family=Great+Vibes&family=Alex+Brush&display=swap" rel="stylesheet">
<style>
:root{
  --pink:#fd4f73;
  --green:#3b7f69;
  --yellow:#fffb8c;
  --magenta:#d93b8e;
  --olive:#8a8a1c;
  --white:#ffffff;
  --sky-top:#b9d6ec;
  --sky-low:#f3f6fa;
  --fresh-top:#a9e3f6;
  --fresh-mid:#eafaf6;
  --fresh-low:#eefab0;
}
*{margin:0;padding:0;box-sizing:border-box}
html,body{width:740px;height:1200px;overflow:hidden;background:var(--white)}
.sheet{position:relative;width:740px;height:1200px}
.post{position:absolute;width:219px;height:274px;overflow:hidden}
.post--yellow{background:var(--yellow)}
.post--fresh{background:linear-gradient(180deg,var(--fresh-top) 0%,var(--fresh-mid) 45%,var(--fresh-low) 100%)}
.post--sky{background:linear-gradient(180deg,var(--sky-top) 0%,var(--sky-low) 55%,var(--white) 100%)}
.line{position:absolute;left:0;right:0;text-align:center;line-height:1;white-space:nowrap}
.serif{font-family:"Playfair Display",serif;font-weight:800}
.sans{font-family:"Montserrat",sans-serif;font-weight:700}
.cond{font-family:"Bebas Neue",sans-serif}
.script{font-family:"Great Vibes",cursive}
.brush{font-family:"Alex Brush",cursive}
.band{position:absolute;color:var(--white);text-align:center;line-height:1;white-space:nowrap;display:flex;align-items:center;justify-content:center}
.frame{position:absolute;left:17px;top:16px;width:186px;height:241px;border:2px solid var(--white)}
.products{position:absolute;border-radius:6px;background:linear-gradient(90deg,#e8e9ee 0%,#fafafa 20%,#e6e8ef 40%,#fafafa 60%,#e8e9ee 80%,#fafafa 100%)}
.person{position:absolute;right:0;bottom:0;width:127px;height:198px;background:linear-gradient(180deg,#4a3128 0%,#8a5c45 25%,#f2efec 45%,#ece8e4 62%,#262626 80%,#d9dde3 100%)}
.florals{position:absolute;right:0;top:0;width:70px;height:50px;background:radial-gradient(circle at 100% 0%,#e7a8cf 0%,#f1cbe0 45%,rgba(255,255,255,0) 75%)}
.florals--low{right:auto;top:auto;left:0;bottom:0;background:radial-gradient(circle at 0% 100%,#e7a8cf 0%,#f1cbe0 45%,rgba(255,255,255,0) 75%)}
.outline-box{position:absolute;text-align:center}
</style>
</head>
<body>
<main class="sheet">

  <!-- Post 1 -->
  <section class="post post--yellow" style="left:21px;top:21px">
    <div style="position:absolute;left:18px;top:16px;width:183px;height:242px;background:var(--white);box-shadow:0 2px 8px rgba(0,0,0,.12)"></div>
    <div class="line serif" style="top:50px;font-size:24px;color:var(--pink)">Mother’s Day</div>
    <div class="band sans" style="left:30px;top:79px;width:158px;height:21px;background:var(--green);font-size:13px;border-radius:2px">SPRING DETOX SALE</div>
    <div class="line" style="top:106px;color:var(--pink)">
      <span class="serif" style="font-size:54px">25</span><span class="serif" style="display:inline-block;font-size:16px;line-height:.9;vertical-align:6px;text-align:left"><span style="font-size:28px">%</span><br>OFF</span>
    </div>
    <div class="line sans" style="top:159px;font-size:13px;color:var(--green)">EVERYTHING!</div>
    <div class="products" role="img" aria-label="Four supplement bottles grouped together" style="left:33px;top:182px;width:154px;height:76px"></div>
  </section>

  <!-- Post 2 -->
  <section class="post post--yellow" style="left:260px;top:21px">
    <div class="line sans" style="top:22px;left:16px;text-align:left;font-size:43px;font-weight:800;color:var(--pink);letter-spacing:-1px">25%OFF</div>
    <div class="line sans" style="top:65px;left:17px;text-align:left;font-size:16px;color:var(--green)">MOTHER’S DAY</div>
    <div class="person" role="img" aria-label="Smiling woman in a white top standing behind a row of supplement bottles"></div>
    <div class="outline-box serif" style="left:16px;top:88px;width:92px;height:95px;border:2px solid var(--pink);background:var(--yellow);color:var(--pink);line-height:.95;padding-top:6px">
      <div style="font-size:24px">Spring</div><div style="font-size:24px">Detox</div><div style="font-size:32px">Sale</div>
    </div>
  </section>

  <!-- Post 3 -->
  <section class="post post--yellow" style="left:500px;top:21px">
    <div class="line serif" style="top:20px;font-size:44px;color:var(--pink)">25%OFF</div>
    <div class="line sans" style="top:65px;font-size:17px;color:var(--green)">ALL SUPPLEMENTS</div>
    <div class="line serif" style="top:82px;font-size:34px;color:var(--green)">Spring</div>
    <div class="line sans" style="top:121px;font-size:24px;font-weight:800;color:var(--pink)">DETOX SALE!</div>
    <div class="products" role="img" aria-label="Four supplement bottles in a row" style="left:14px;top:163px;width:192px;height:82px"></div>
  </section>

  <!-- Post 4 -->
  <section class="post post--fresh" style="left:21px;top:315px">
    <div class="line cond" style="top:18px;font-size:54px;color:var(--pink)">25%OFF</div>
    <div class="line script" style="top:58px;font-size:44px;color:var(--green)">Spring</div>
    <div class="line cond" style="top:106px;font-size:40px;color:var(--green)">DETOX SALE</div>
    <div class="band cond" style="left:20px;top:145px;width:180px;height:17px;background:var(--pink);font-size:16px;border-radius:2px">SPRING RESET. SUMMER READY</div>
    <div class="products" role="img" aria-label="Four supplement bottles in a row" style="left:17px;top:172px;width:188px;height:80px"></div>
  </section>

  <!-- Post 5 -->
  <section class="post post--fresh" style="left:260px;top:315px">
    <div class="line cond" style="top:18px;font-size:54px;color:var(--pink)">25%OFF</div>
    <div class="person" role="img" aria-label="Smiling woman in a white top standing behind a row of supplement bottles"></div>
    <div class="line cond" style="top:68px;left:20px;text-align:left;font-size:28px;color:var(--green)">EVERYTHING</div>
    <div class="band cond" style="left:21px;top:96px;width:112px;height:23px;background:var(--pink);font-size:21px;border-radius:2px">MOTHER’S DAY</div>
    <div class="outline-box" style="left:21px;top:128px;width:69px;height:85px;border:1.5px solid var(--green);background:rgba(255,255,255,.35);line-height:.9;padding-top:4px">
      <div class="script" style="font-size:26px;color:var(--green)">Spring</div>
      <div class="cond" style="font-size:24px;color:var(--pink)">DETOX</div>
      <div class="cond" style="font-size:30px;color:var(--pink)">SALE</div>
    </div>
  </section>

  <!-- Post 6 -->
  <section class="post post--fresh" style="left:500px;top:315px">
    <div class="line cond" style="top:18px;font-size:54px;color:var(--pink)">25%OFF</div>
    <div class="line cond" style="top:68px;font-size:34px;color:var(--green)">MOTHER’S DAY</div>
    <div class="line script" style="top:94px;font-size:34px;color:var(--pink)">Sale</div>
    <div class="band cond" style="left:20px;top:131px;width:179px;height:23px;background:var(--green);font-size:22px;border-radius:2px">FEEL AMAZING AGAIN!</div>
    <div class="products" role="img" aria-label="Four supplement bottles grouped together" style="left:22px;top:160px;width:178px;height:96px"></div>
  </section>

  <!-- Post 7 -->
  <section class="post post--sky" style="left:21px;top:609px">
    <div class="florals" role="img" aria-label="Pink spring blossoms in the corner"></div>
    <div class="frame"></div>
    <div class="line" style="top:24px;left:20px;color:var(--magenta)">
      <span class="sans" style="font-size:78px;font-weight:600">25</span><span class="sans" style="display:inline-block;font-size:19px;font-weight:500;line-height:.95;vertical-align:4px;text-align:left"><span style="font-size:40px">%</span><br>OFF</span>
    </div>
    <div class="line sans" style="top:98px;font-size:17px;font-weight:500;color:var(--olive)">MOTHER’S DAY</div>
    <div class="line brush" style="top:112px;font-size:32px;color:var(--olive)">Sale</div>
    <div class="band sans" style="left:42px;top:146px;width:133px;height:19px;background:var(--magenta);font-size:11px;font-weight:600;border-radius:2px">REFRESH YOUR BODY</div>
    <div class="products" role="img" aria-label="Four supplement bottles grouped together" style="left:33px;top:170px;width:154px;height:88px"></div>
  </section>

  <!-- Post 8 -->
  <section class="post post--sky" style="left:260px;top:609px">
    <div class="florals" role="img" aria-label="Pink spring blossoms in the corner"></div>
    <div class="frame"></div>
    <div class="line" style="top:24px;left:29px;text-align:left;color:var(--magenta)">
      <span class="sans" style="font-size:64px;font-weight:600">25</span><span class="sans" style="display:inline-block;font-size:16px;font-weight:500;line-height:.95;vertical-align:4px;text-align:left"><span style="font-size:34px">%</span><br>OFF</span>
    </div>
    <div class="person" role="img" aria-label="Smiling woman in a white top standing behind a row of supplement bottles"></div>
    <div class="outline-box" style="left:31px;top:86px;width:68px;height:80px;border:1.5px solid var(--olive);line-height:.9;padding-top:3px">
      <div class="script" style="font-size:24px;color:var(--olive)">Spring</div>
      <div class="cond" style="font-size:23px;color:var(--magenta)">DETOX</div>
      <div class="cond" style="font-size:28px;color:var(--magenta)">SALE</div>
    </div>
    <div class="line cond" style="top:173px;left:30px;text-align:left;font-size:14px;color:var(--olive);line-height:1.05">SPRING CLEANSE.<br><span style="color:var(--magenta)">SUMMER GLOW</span></div>
  </section>

  <!-- Post 9 -->
  <section class="post post--sky" style="left:500px;top:609px">
    <div class="florals" role="img" aria-label="Pink spring blossoms in the corner"></div>
    <div class="frame"></div>
    <div class="line sans" style="top:33px;font-size:50px;font-weight:600;color:var(--magenta);letter-spacing:-1px">25%off</div>
    <div class="band cond" style="left:29px;top:85px;width:162px;height:23px;background:var(--olive);font-size:22px;border-radius:2px">MOTHER’S DAY SALE</div>
    <div class="line cond" style="top:111px;font-size:25px;color:var(--magenta)">DETOX THIS SPRING</div>
    <div class="line brush" style="top:133px;font-size:25px;color:var(--olive)">Shine This Summer</div>
    <div class="products" role="img" aria-label="Four supplement bottles in a row" style="left:16px;top:173px;width:189px;height:81px"></div>
  </section>

  <!-- Post 10 -->
  <section class="post post--sky" style="left:21px;top:903px">
    <div class="florals" role="img" aria-label="Pink spring blossoms in the top corner"></div>
    <div class="florals florals--low" role="img" aria-label="Pink spring blossoms in the bottom corner"></div>
    <div class="frame"></div>
    <div class="line sans" style="top:33px;font-size:50px;font-weight:600;color:var(--magenta);letter-spacing:-1px">25%off</div>
    <div class="band cond" style="left:30px;top:83px;width:157px;height:22px;background:var(--olive);font-size:22px;border-radius:2px">MOTHER’S DAY SALE</div>
    <div class="line script" style="top:104px;font-size:38px;color:var(--magenta)">Spring</div>
    <div class="line cond" style="top:145px;font-size:32px;color:var(--olive)">DETOX</div>
    <div class="band cond" style="left:90px;top:176px;width:40px;height:19px;background:var(--magenta);font-size:16px;border-radius:2px">FOR A</div>
    <div class="line cond" style="top:199px;font-size:32px;color:var(--magenta)">SUMMER BODY</div>
  </section>

</main>
</body>
</html>
```